Business Card Design

Just looking for a good designs that looks good with our company logo. I'd like it to be simple and to the point. Just including contact information, our logo, and my name somewhere on the card so future clients know who they're contacting, and a couple services offered. The two images I attached are pictures of our logo. I don't care which color they they are, I just attached both images to give a reference of logo colors depending on the color of the card.
Names: Carl Whitby
Phone: 816-555-0147
Email: greenstripeyard@fernmail.test
Services offered:
Mowing
Fertilization
Aeration
Bed & tree maintenance
and more.
Business
Names: Carl Whitby
Phone: 816-555-0147
(no website)

```html
<!DOCTYPE html>
<html lang="en">
<head>
<meta charset="utf-8">
<title>Greenstripe Yard – Business Card</title>
<link rel="stylesheet" href="https://fonts.googleapis.com/css2?family=Open+Sans:wght@400;600;700&display=swap">
<style>
  :root {
    --page-bg: #e9e9e9;
    --card-dark: #1f1f20;
    --grass-light: #5fae2c;
    --grass-mid: #3f8a1c;
    --grass-deep: #2c6a12;
    --accent-red: #e0262b;
    --text-light: #e6e6e6;
    --text-dark: #1d2a12;
  }
  * { box-sizing: border-box; margin: 0; padding: 0; }
  html, body {
    width: 1200px; height: 1200px; overflow: hidden;
    background: var(--page-bg);
    font-family: "Open Sans", Arial, sans-serif;
  }
  .business-card {
    position: absolute;
    left: 75px; top: 300px;
    width: 1050px; height: 600px;
    background: var(--card-dark);
    overflow: hidden;
    box-shadow: 0 14px 40px rgba(0,0,0,.22);
  }
  .grass-field {
    position: absolute; inset: 0;
    background: linear-gradient(175deg, var(--grass-deep) 0%, var(--grass-light) 45%, var(--grass-mid) 100%);
    clip-path: polygon(0 36%, 100% 80%, 100% 100%, 0 100%);
  }
  .brand {
    position: absolute; left: 120px; top: 70px;
    display: flex; align-items: center; gap: 22px;
  }
  .brand-dot {
    width: 70px; height: 70px; border-radius: 50%;
    background: var(--accent-red);
  }
  .brand-name {
    font-weight: 700; font-size: 56px; color: var(--text-light);
    letter-spacing: 1px;
  }
  .services {
    position: absolute; left: 640px; top: 190px;
    color: var(--text-light); list-style: none;
    font-size: 27px; line-height: 1.3;
  }
  .services-title { font-size: 21px; margin-left: 38px; margin-bottom: 4px; }
  .services li { display: flex; align-items: center; gap: 12px; }
  .services li.more { margin-left: 38px; }
  .tick { width: 24px; height: 24px; flex: none; }
  .contact {
    position: absolute; left: 110px; top: 350px;
    color: var(--text-dark);
  }
  .contact-name { font-weight: 700; font-size: 34px; margin-bottom: 14px; }
  .contact-line {
    display: flex; align-items: center; gap: 12px;
    font-size: 27px; margin-left: 250px; line-height: 1.45;
  }
  .contact-icon { width: 26px; height: 26px; flex: none; }
</style>
</head>
<body>
  <div class="business-card">
    <div class="grass-field" role="img" aria-label="Photo of a freshly mown green lawn"></div>

    <div class="brand">
      <span class="brand-dot"></span>
      <span class="brand-name">Greenstripe Yard</span>
    </div>

    <ul class="services">
      <li class="services-title">Services offered:</li>
      <li><svg class="tick" viewBox="0 0 24 24"><rect width="24" height="24" rx="3" fill="#e0262b"/><path d="M5 12l5 5 9-10" fill="none" stroke="#fff" stroke-width="3"/></svg>Mowing</li>
      <li><svg class="tick" viewBox="0 0 24 24"><rect width="24" height="24" rx="3" fill="#e0262b"/><path d="M5 12l5 5 9-10" fill="none" stroke="#fff" stroke-width="3"/></svg>Fertilization</li>
      <li><svg class="tick" viewBox="0 0 24 24"><rect width="24" height="24" rx="3" fill="#e0262b"/><path d="M5 12l5 5 9-10" fill="none" stroke="#fff" stroke-width="3"/></svg>Aeration</li>
      <li><svg class="tick" viewBox="0 0 24 24"><rect width="24" height="24" rx="3" fill="#e0262b"/><path d="M5 12l5 5 9-10" fill="none" stroke="#fff" stroke-width="3"/></svg>Bed &amp; tree maintenance</li>
      <li class="more">and more.</li>
    </ul>

    <div class="contact">
      <p class="contact-name">Carl Whitby</p>
      <p class="contact-line">
        <svg class="contact-icon" viewBox="0 0 24 24"><rect width="24" height="24" rx="4" fill="#e0262b"/><path d="M8 5h3l1 4-2 1.5a9 9 0 0 0 3.5 3.5L15 12l4 1v3a2 2 0 0 1-2 2A12 12 0 0 1 6 7a2 2 0 0 1 2-2z" fill="#fff"/></svg>
        816-555-0147
      </p>
      <p class="contact-line">
        <svg class="contact-icon" viewBox="0 0 24 24"><rect width="24" height="24" rx="4" fill="#e0262b"/><rect x="5" y="7" width="14" height="10" fill="#fff"/><path d="M5 7l7 6 7-6" fill="none" stroke="#e0262b" stroke-width="1.6"/></svg>
        greenstripeyard@fernmail.test
      </p>
    </div>
  </div>
</body>
</html>
```